Professional and creative business card design for recruiting service providers

Our company supports German medium-sized companies in filling vacancies promptly. For this we use social media marketing and bring our customers into the visibility.

We want a professional but also creative design for our business cards.

Please look at lindqvar-staff.de to get an impression of our CI.

Target Market(s)

Small and medium-sized companies in Germany from the industry

Industry/Entity Type

Industrie, Handwerk

Contact Information for Business Card

Name, Position, Telefonnummer, Email, Website

Colors
EE7325
F08F49
F5BC92
FAE3D3
FDF4ED

Requirements
Must have
• A picture of the employee and in the style of www.lindqvar-staff.de

```html
<!DOCTYPE html>
<html lang="en">
<head>
<meta charset="utf-8">
<title>Lindqvar &amp; Staff – Business Card</title>
<link rel="stylesheet" href="https://fonts.googleapis.com/css2?family=Montserrat:wght@700;800&family=Roboto:wght@400;500&display=swap">
<style>
  :root {
    --orange: #EE7325;
    --orange-light: #F08F49;
    --peach: #F5BC92;
    --cream: #FAE3D3;
    --ink: #161616;
    --paper: #ffffff;
    --backdrop: #c4c4c4;
    --photo-tone: #dcdadd;
  }
  * { box-sizing: border-box; margin: 0; padding: 0; }
  html, body { width: 1200px; height: 800px; overflow: hidden; }
  body {
    background: var(--backdrop);
    position: relative;
    font-family: "Roboto", Arial, sans-serif;
  }
  .card {
    position: absolute;
    left: 292px;
    width: 616px;
    height: 352px;
    border-radius: 3px;
    overflow: hidden;
  }
  .card-front { top: 32px; background: var(--paper); border: 2px solid var(--orange); }
  .card-back { top: 416px; background: var(--orange); }

  .brand {
    position: absolute;
    left: 40px;
    top: 44px;
    display: flex;
    align-items: center;
    gap: 14px;
  }
  .brand-mark { width: 26px; height: 26px; background: var(--orange); }
  .brand-name {
    font-family: "Montserrat", Arial, sans-serif;
    font-weight: 800;
    font-size: 24px;
    line-height: 1.05;
    letter-spacing: 1.5px;
    color: var(--ink);
    text-transform: uppercase;
  }

  .person { position: absolute; left: 40px; top: 156px; }
  .person-name {
    font-family: "Montserrat", Arial, sans-serif;
    font-weight: 800;
    font-size: 25px;
    letter-spacing: 0.5px;
    color: var(--orange);
    text-transform: uppercase;
  }
  .person-role { font-size: 16px; color: var(--ink); margin-top: 2px; }

  .contact { position: absolute; left: 40px; top: 232px; list-style: none; }
  .contact li {
    display: flex; align-items: center; gap: 8px;
    font-size: 15.5px; color: var(--ink); line-height: 26px;
  }
  .contact svg { width: 15px; height: 15px; flex: none; }
  .contact .accent { color: var(--orange); }

  .photo-frame {
    position: absolute;
    right: 34px;
    top: 40px;
    width: 250px;
    height: 268px;
    border: 2px solid var(--orange);
    background: linear-gradient(160deg, var(--photo-tone) 0%, #cfcbcd 55%, #4a4a52 100%);
  }

  .back-brand {
    position: absolute;
    inset: 0;
    display: flex;
    align-items: center;
    justify-content: center;
    gap: 22px;
  }
  .back-brand .brand-mark { width: 54px; height: 54px; background: var(--orange-light); }
  .back-brand .brand-name { font-size: 42px; color: var(--orange-light); letter-spacing: 3px; }
</style>
</head>
<body>
  <section class="card card-front">
    <div class="brand">
      <span class="brand-mark"></span>
      <span class="brand-name">Lindqvar<br>&amp; Staff</span>
    </div>

    <div class="person">
      <h1 class="person-name">Jonas Hartwig</h1>
      <p class="person-role">Managing Director</p>
    </div>

    <ul class="contact">
      <li>
        <svg viewBox="0 0 16 16"><path fill="var(--orange)" d="M4 1.5l2.2 3-1.3 1.6a8 8 0 0 0 5 5l1.6-1.3 3 2.2-1.4 2.4C7.5 14 2 8.5 1.6 2.9z"/></svg>
        030-555 218 400
      </li>
      <li>
        <svg viewBox="0 0 16 16"><rect x="1" y="3" width="14" height="10" fill="var(--orange)"/><path d="M1 3l7 6 7-6" fill="none" stroke="#fff" stroke-width="1.4"/></svg>
        info@lindqvar-staff.de
      </li>
      <li>
        <svg viewBox="0 0 16 16"><circle cx="8" cy="8" r="6.5" fill="none" stroke="var(--orange)" stroke-width="1.6"/><path d="M1.5 8h13M8 1.5c-3 3.5-3 9.5 0 13M8 1.5c3 3.5 3 9.5 0 13" fill="none" stroke="var(--orange)" stroke-width="1.2"/></svg>
        <span>www.<span class="accent">lindqvar-staff</span>.de</span>
      </li>
    </ul>

    <div class="photo-frame" role="img" aria-label="Portrait photo of the employee in a dark blazer and white shirt on a light grey background"></div>
  </section>

  <section class="card card-back">
    <div class="back-brand">
      <span class="brand-mark"></span>
      <span class="brand-name">Lindqvar<br>&amp; Staff</span>
    </div>
  </section>
</body>
</html>
```